Dermal Care Nursing Circle - Rack Card Design

This is a 2-sided rack card that should be 3.5 inches wide by 8.5 inches tall.

Text (with instructions), logo and website image are attached. For the main image on the front, you can use the attached image, or pull whatever you like off of pictovault.example, and we will purchase the photo from the winning design

The front should have text plus a nurse image, the back should have mostly text with the website image and legend.
Updates

We have received many high quality designs, but it is apparent to us that at the print size we are currently using (3.5x8.5), that the image of the homepage on the back is too small, and not legible. As such, we have decided that we would like to go with a horizontal version at 8.5 wide by 5.5 tall, with a larger more legible version of the website on the back and call outs to one side or the other, please resubmit your designs in that format. Thank you, and sorry for the inconvenience. Ned

Industry/Entity Type

Nurse

Font styles to use
Sans Serif

Colors
876aae
6b449b
b7a5cd
e4daeb

Requirements
Must have
• Please use the color palate from the attached logo, and a nursing image on the front.

```html
<!DOCTYPE html>
<html lang="en">
<head>
<meta charset="utf-8">
<title>Dermal Care Nursing Circle – Rack Card</title>
<link rel="stylesheet" href="https://fonts.googleapis.com/css2?family=Ubuntu:wght@400;500&family=Mulish:wght@400;600&display=swap">
<style>
  :root{
    --purple:#6b449b;
    --purple-dark:#4b2d78;
    --lavender:#876aae;
    --lilac:#b7a5cd;
    --mist:#e4daeb;
    --row:#e6e6e8;
    --band-grey:#8a8a8c;
    --ink:#4a4a4c;
    --soft:#8d8d90;
    --page:#ecebee;
  }
  *{box-sizing:border-box;margin:0;padding:0}
  html,body{width:960px;height:1200px;overflow:hidden}
  body{background:var(--page);font-family:"Mulish",sans-serif;color:var(--ink);position:relative}
  .card{position:absolute;left:80px;width:800px;height:518px;background:#fff;overflow:hidden;box-shadow:0 2px 8px rgba(0,0,0,.18)}
  .card--front{top:82px}
  .card--back{top:634px}

  /* front */
  .brand{position:absolute;left:0;top:0;width:294px;height:104px;display:flex;align-items:center;justify-content:center;gap:10px}
  .brand__foundation,.brand__name{font-family:"Ubuntu",sans-serif;font-weight:500;color:var(--purple);line-height:1.1}
  .brand__foundation{font-size:15px;text-align:right;width:96px}
  .brand__rule{width:1px;height:60px;background:var(--purple)}
  .brand__name{font-size:17px;width:130px}
  .headline{position:absolute;left:294px;top:0;right:0;height:104px;background:var(--purple);color:#fff;font-family:"Ubuntu",sans-serif;font-weight:400;font-size:23px;line-height:1.3;padding:25px 0 0 25px;white-space:nowrap}
  .hero-photo{position:absolute;left:0;top:104px;right:0;bottom:0;background:linear-gradient(180deg,#c58f72 0%,#a7674c 30%,#3a4c8e 62%,#223070 100%)}

  /* back: website mockup */
  .site{position:absolute;left:8px;top:13px;width:418px;height:491px;border:1.5px solid #6d6d70;background:#f7f7f8}
  .site__nav{position:absolute;left:0;top:0;right:0;height:34px;background:#fff;display:flex;align-items:center}
  .site__logo{font-family:"Ubuntu",sans-serif;font-weight:500;color:var(--purple);font-size:6.5px;line-height:1.1;margin-left:48px;width:60px}
  .site__menu{display:flex;gap:8px;font-size:3.6px;color:#777;text-transform:uppercase;margin-left:10px}
  .site__menu span{padding:3px 0}
  .site__menu .is-active{background:var(--lavender);color:#fff;padding:3px 4px}
  .site__photo{position:absolute;left:10px;top:45px;width:179px;height:132px;background:linear-gradient(180deg,#c28b6e 0%,#9a644d 35%,#34478a 70%,#243272 100%)}
  .site__photo-band{position:absolute;left:10px;top:137px;width:179px;height:18px;background:var(--purple)}
  .search{position:absolute;left:218px;top:41px;font-size:5.5px;color:#333}
  .search__title{font-size:6.5px;font-weight:600;margin-bottom:6px}
  .search__label{font-size:4.2px;margin:3px 0}
  .search__btn{display:block;width:52px;height:13px;background:var(--lavender);color:#fff;font-size:3.6px;line-height:13px;padding-left:5px;margin:0 0 8px;white-space:nowrap}
  .anatomy{position:absolute;left:300px;top:45px;width:52px;height:132px;background:radial-gradient(ellipse at 50% 50%,#c79aa3 0%,#d7c8da 55%,#f7f7f8 80%)}
  .tag{position:absolute;background:var(--purple);color:#fff;font-family:"Ubuntu",sans-serif;font-size:14px;line-height:1;padding:3px 6px}
  .rule-h{position:absolute;height:1px;background:#c9c9cc}
  .rule-v{position:absolute;width:1px;background:#c9c9cc}
  .feature{position:absolute;text-align:center}
  .feature__title{font-size:9.5px;color:var(--purple-dark);line-height:1.2}
  .feature__text{font-size:6.5px;color:var(--soft);line-height:1.2;margin-top:2px}
  .note{position:absolute;font-size:6.5px;color:var(--soft);line-height:1.2}
  .icon{position:absolute;color:var(--purple-dark)}
  .leadership-art{position:absolute;left:308px;top:300px;width:68px;height:56px;background:linear-gradient(135deg,#e4daeb,#876aae)}

  /* back: legend */
  .intro{position:absolute;left:426px;top:14px;width:374px;height:41px;background:var(--band-grey);color:#fff;font-family:"Ubuntu",sans-serif;font-size:10.8px;line-height:1.3;padding:7px 8px 0 14px;white-space:nowrap}
  .legend{position:absolute;left:450px;width:350px;background:var(--row)}
  .legend__letter{position:absolute;left:8px;top:6px;font-family:"Ubuntu",sans-serif;font-size:11px;color:#333}
  .legend__icon{position:absolute;left:28px;width:52px;height:52px;top:50%;margin-top:-26px;background:#fff;display:flex;align-items:center;justify-content:center;color:var(--purple-dark)}
  .legend__divider{position:absolute;left:84px;top:6px;bottom:6px;border-left:1.5px dashed var(--purple)}
  .legend__text{position:absolute;left:102px;right:20px;top:50%;transform:translateY(-50%);font-size:10.4px;line-height:1.3;color:#555;text-align:justify}
  .legend__body{width:14px;height:44px;background:linear-gradient(180deg,#d7b4b8,#a57aa0)}
  .more{position:absolute;right:32px;top:464px;font-size:11.6px;color:#333}
  .url{position:absolute;left:520px;top:490px;width:280px;height:28px;background:var(--purple);clip-path:polygon(10px 0,100% 0,100% 100%,0 100%);color:#fff;font-family:"Ubuntu",sans-serif;font-size:16px;display:flex;align-items:center;justify-content:flex-end;gap:8px;padding-right:18px}
</style>
</head>
<body>

<svg width="0" height="0" style="position:absolute" aria-hidden="true">
  <defs>
    <symbol id="i-news" viewBox="0 0 40 40">
      <rect x="4" y="8" width="32" height="24" rx="3" fill="none" stroke="currentColor" stroke-width="3"/>
      <rect x="9" y="13" width="9" height="8" fill="currentColor"/>
      <path d="M21 14h10M21 18h10M9 24h22M9 27.5h22" stroke="currentColor" stroke-width="2"/>
    </symbol>
    <symbol id="i-kit" viewBox="0 0 40 40">
      <path d="M15 11V7h10v4" fill="none" stroke="currentColor" stroke-width="3"/>
      <rect x="4" y="11" width="32" height="24" rx="4" fill="currentColor"/>
      <circle cx="20" cy="23" r="7.5" fill="#fff"/>
      <path d="M20 19v8M16 23h8" stroke="currentColor" stroke-width="3"/>
    </symbol>
    <symbol id="i-clip" viewBox="0 0 40 40">
      <rect x="9" y="6" width="22" height="30" rx="2" fill="none" stroke="currentColor" stroke-width="2.5"/>
      <rect x="15" y="3" width="10" height="6" rx="1" fill="currentColor"/>
      <circle cx="20" cy="22" r="7" fill="currentColor"/>
      <path d="M20 17.5v7M16.5 21.5l3.5 3.5 3.5-3.5M16 27h8" fill="none" stroke="#fff" stroke-width="1.8"/>
    </symbol>
    <symbol id="i-chat" viewBox="0 0 40 40">
      <circle cx="20" cy="18" r="15" fill="currentColor"/>
      <path d="M22 31l10 7-3-10z" fill="currentColor"/>
      <circle cx="15.5" cy="14" r="3.6" fill="#fff"/>
      <circle cx="24.5" cy="14" r="3.6" fill="#fff"/>
      <path d="M9 25c0-5 3-7 6.5-7s6.5 2 6.5 7zM18 25c0-5 3-7 6.5-7S31 20 31 25z" fill="#fff"/>
    </symbol>
    <symbol id="i-mouse" viewBox="0 0 40 40">
      <g transform="rotate(-35 16 24)">
        <rect x="7" y="13" width="18" height="24" rx="9" fill="currentColor"/>
        <path d="M7 23h18M16 13v10" stroke="#fff" stroke-width="1.8"/>
      </g>
      <path d="M21 13c4-7 10-9 13-6s-1 8-6 9" fill="none" stroke="currentColor" stroke-width="2.5"/>
    </symbol>
    <symbol id="i-globe" viewBox="0 0 20 20">
      <circle cx="10" cy="10" r="8" fill="none" stroke="currentColor" stroke-width="1.6"/>
      <ellipse cx="10" cy="10" rx="3.5" ry="8" fill="none" stroke="currentColor" stroke-width="1.3"/>
      <path d="M2 10h16M3.5 6h13M3.5 14h13" stroke="currentColor" stroke-width="1.2"/>
    </symbol>
  </defs>
</svg>

<!-- Front -->
<section class="card card--front">
  <div class="brand">
    <div class="brand__foundation">Skin Path Foundation</div>
    <div class="brand__rule"></div>
    <div class="brand__name">Dermal Care<br>Nursing<br>Circle</div>
  </div>
  <h1 class="headline">INSPIRED BY PATIENTS EMPOWERED<br>BY KNOWLEDGE IMPACTING MELANOMA</h1>
  <div class="hero-photo" role="img" aria-label="Photo of four smiling nurses in navy scrubs with arms crossed in front of a hospital building"></div>
</section>

<!-- Back -->
<section class="card card--back">
  <div class="site">
    <div class="site__nav">
      <div class="site__logo">Dermal Care<br>Nursing Circle</div>
      <nav class="site__menu">
        <span class="is-active">Home</span><span>About</span><span>Nurse Resources</span><span>Side Effect Search</span><span>Education</span><span>Patient Resources</span><span>News</span><span>Contact</span>
      </nav>
    </div>
    <div class="site__photo" role="img" aria-label="Homepage photo of four nurses in navy scrubs"></div>
    <div class="site__photo-band"></div>

    <div class="search">
      <div class="search__title">Search for side effects</div>
      <div class="search__label">By body location:</div>
      <div class="search__label">Patient is on:</div>
      <span class="search__btn">Immunotherapy</span>
      <span class="search__btn">Targeted therapy</span>
      <span class="search__btn">Intralesional</span>
      <div class="search__label">By traditional search:</div>
      <span class="search__btn">SEARCH BY DRUG</span>
      <span class="search__btn">SEARCH BY SYMPTOM</span>
    </div>
    <div class="anatomy" role="img" aria-label="Anatomical illustration of the human body"></div>
    <span class="tag" style="left:354px;top:45px;width:64px">B.</span>

    <div class="rule-h" style="left:12px;top:189px;width:394px"></div>

    <svg class="icon" style="left:48px;top:193px" width="30" height="30"><use href="#i-news"/></svg>
    <div class="feature" style="left:0;top:240px;width:126px">
      <div class="feature__title">Nursing Consensus<br>Statements from <i>CRDN</i></div>
      <div class="feature__text">Practical approaches to help<br>dermal patients achieve<br>optimal benefit from therapies</div>
    </div>

    <div class="rule-v" style="left:133px;top:205px;height:112px"></div>

    <span class="tag" style="left:142px;top:206px">C.</span>
    <svg class="icon" style="left:182px;top:202px" width="38" height="38"><use href="#i-kit"/></svg>
    <div class="feature" style="left:140px;top:250px;width:128px">
      <div class="feature__title">Nurse Toolkit</div>
      <div class="feature__text">Download quick and easy<br>resources to advance the nursing<br>care of dermal patients</div>
    </div>

    <div class="rule-v" style="left:274px;top:205px;height:284px"></div>

    <span class="tag" style="left:278px;top:206px">F.</span>
    <svg class="icon" style="left:320px;top:203px" width="38" height="38"><use href="#i-mouse"/></svg>
    <div class="feature" style="left:278px;top:252px;width:128px">
      <div class="feature__title">Education</div>
      <div class="feature__text">Stay up-to-date on dermal patient<br>care with free online education<br>modules and events</div>
    </div>

    <div class="rule-h" style="left:280px;top:295px;width:118px"></div>

    <div class="leadership-art" role="img" aria-label="Illustration of figures climbing an upward arrow toward a flag"></div>
    <div class="feature" style="left:278px;top:364px;width:128px">
      <div class="feature__title">MEET THE DCNC<br>LEADERSHIP BOARD</div>
      <div class="feature__text">Experts empowering nurses with<br>tools to improve patient outcomes in<br>dermal care</div>
    </div>
    <div class="feature" style="left:278px;top:420px;width:128px"><div class="feature__text">NEWS</div></div>
    <span class="tag" style="left:278px;top:438px">A.</span>
    <svg class="icon" style="left:322px;top:433px" width="36" height="30"><use href="#i-news"/></svg>
    <div class="feature" style="left:278px;top:469px;width:128px"><div class="feature__text">Get the latest news on dermal care</div></div>

    <span class="tag" style="left:0;top:330px">E.</span>
    <svg class="icon" style="left:42px;top:328px" width="52" height="52"><use href="#i-chat"/></svg>
    <div class="note" style="left:104px;top:332px">Share challenges, insights, and solutions<br>with other nurses in our<br>online community</div>
    <div class="feature" style="left:8px;top:383px;width:120px"><div class="feature__title">Q&amp;A Community</div></div>

    <div class="rule-h" style="left:9px;top:403px;width:205px"></div>

    <span class="tag" style="left:0;top:422px">D.</span>
    <svg class="icon" style="left:44px;top:420px" width="34" height="36"><use href="#i-clip"/></svg>
    <div class="note" style="left:104px;top:432px">Educate and engage patients with<br>with information on specific therapies</div>
    <div class="feature" style="left:0;top:462px;width:126px"><div class="feature__title">Printable<br>Patient Materials</div></div>
    <div class="note" style="left:170px;top:474px;color:#d5d5d8">Download patient handouts</div>
  </div>

  <p class="intro">You wear many hats and take care of patients with many different<br>skin types. Visit DermalCareCircle.example for free access to:</p>

  <div class="legend" style="top:72px;height:68px">
    <span class="legend__letter">A.</span>
    <span class="legend__icon"><svg width="38" height="38"><use href="#i-news"/></svg></span>
    <span class="legend__divider"></span>
    <p class="legend__text">Hot off the press! Articles from the Clinical Review of Dermal Nursing outlining practical strategies to manage side-effects and promote adherence to dermal therapies</p>
  </div>
  <div class="legend" style="top:144px;height:59px">
    <span class="legend__letter">B.</span>
    <span class="legend__icon"><span class="legend__body" role="img" aria-label="Small anatomical body illustration"></span></span>
    <span class="legend__divider"></span>
    <p class="legend__text">Visual and text-based therapeutic side effect management tools</p>
  </div>
  <div class="legend" style="top:207px;height:60px">
    <span class="legend__letter">C.</span>
    <span class="legend__icon"><svg width="40" height="40"><use href="#i-kit"/></svg></span>
    <span class="legend__divider"></span>
    <p class="legend__text">A Nurse’s Toolkit with extensive dermal nursing care resources</p>
  </div>
  <div class="legend" style="top:271px;height:59px">
    <span class="legend__letter">D.</span>
    <span class="legend__icon"><svg width="38" height="40"><use href="#i-clip"/></svg></span>
    <span class="legend__divider"></span>
    <p class="legend__text">Printable patient resources to provide patients, organized by therapy</p>
  </div>
  <div class="legend" style="top:334px;height:60px">
    <span class="legend__letter">E.</span>
    <span class="legend__icon"><svg width="40" height="40"><use href="#i-chat"/></svg></span>
    <span class="legend__divider"></span>
    <p class="legend__text">An oncology nurse community forum to share successes, challenges, insights, and solutions</p>
  </div>
  <div class="legend" style="top:398px;height:60px">
    <span class="legend__letter">F.</span>
    <span class="legend__icon"><svg width="40" height="40"><use href="#i-mouse"/></svg></span>
    <span class="legend__divider"></span>
    <p class="legend__text">Online educational modules, newsfeeds, and other material to keep you up to date</p>
  </div>

  <p class="more">and much more!</p>
  <div class="url"><svg width="14" height="14"><use href="#i-globe"/></svg>www.DermalCareCircle.example</div>
</section>

</body>
</html>
```